PitchTally Webpages and Logo

See attached brief. Take the existing website www.pitchtally.co.uk and logo and transform these assets to:

Give people who arrive on the site for first time the confidence to sign-up easily and quickly
Allow regular returning users quick and easy placing of predictions and encourage them to share the PitchTally prediction on social networks and with their contacts
Convey the essence of a community working together to enjoyably come-up with smart predictions on sporting events
Work seamlessly and well across smartphones, tablets and desktop i.e. Should be Responsive Web Design
Updates

Target Market(s)

Users are sports fans with opinions
Primarily male and early twenties to mid-thirties
They are competitive - they want to beat their peers
Many are from outside the UK

Industry/Entity Type

Events

Logo Text

PitchTally

Coding

Coded - Design and coding required

Number of Pages Required

4 page

Font styles to use
Sans Serif

Requirements
Must have
• Responsive Web Design
• Mobile First
• HTML must work with dedicated bespoke application developed in ASP.NET using MS SQL underneath
• See Brief
Nice to have
• See brief
Should not have
• See brief

```html
<!DOCTYPE html>
<html lang="en">
<head>
<meta charset="utf-8">
<title>PitchTally – Altogether Better Predictions</title>
<link href="https://fonts.googleapis.com/css2?family=Bebas+Neue&family=PT+Sans:wght@400;700&family=Arimo&display=swap" rel="stylesheet">
<style>
:root{
  --teal:#27a594;
  --blue:#4d9fcc;
  --gold:#d6b45a;
  --nav-bg:#2e2f31;
  --footer-bg:#323334;
  --ink:#2b2b2b;
  --card-bg:#f3f3f3;
  --white:#ffffff;
  --muted:#a9a9a9;
}
*{box-sizing:border-box;margin:0;padding:0}
html,body{width:1010px;height:1200px;overflow:hidden;background:var(--white)}
body{font-family:"PT Sans",sans-serif;color:var(--ink);position:relative}

.topbar{position:absolute;left:0;top:0;width:1010px;height:55px;background:var(--nav-bg)}
.brand{position:absolute;left:50px;top:16px;display:flex;align-items:center;gap:8px;color:var(--teal);font-weight:700;font-size:17px}
.brand-dot{width:20px;height:20px;border-radius:50%;background:var(--teal)}
.main-nav a{position:absolute;top:14px;height:28px;line-height:28px;color:var(--white);font-size:11.5px;text-decoration:none;transform:translateX(-50%)}
.main-nav a.is-active{background:var(--teal);border-radius:14px;width:68px;text-align:center}
.signin{position:absolute;left:749px;top:14px;width:76px;height:28px;border-radius:8px;background:var(--blue);color:var(--white);font-size:11.5px;font-weight:700;line-height:28px;text-align:center}
.search{position:absolute;left:835px;top:14px;width:123px;height:28px;border-radius:14px;background:#232425;color:#8a8a8a;font-size:11px;line-height:28px;padding-left:26px}
.search svg{position:absolute;left:10px;top:8px}

.hero{position:absolute;left:0;top:55px;width:1010px;height:505px}
.hero-photo{position:absolute;inset:0;background:radial-gradient(ellipse at 55% 40%,#6b6a63 0%,#4a4943 45%,#2d2d2a 100%)}
.hero-title{position:absolute;top:45px;width:100%;text-align:center;font-family:"Bebas Neue",sans-serif;font-size:52px;color:var(--white);letter-spacing:1px}
.hero-lead{position:absolute;top:120px;left:205px;width:600px;text-align:center;font-size:18.5px;line-height:26.5px;color:var(--white)}
.join{position:absolute;left:443px;top:225px;width:124px;height:37px;border-radius:19px;background:var(--teal);color:var(--white);font-weight:700;font-size:14px;line-height:37px;text-align:center;letter-spacing:.5px}
.step{position:absolute;top:309px;width:300px;text-align:center;color:var(--white)}
.step-icon{width:74px;height:74px;border-radius:50%;margin:0 auto;display:flex;align-items:center;justify-content:center}
.step h2{font-family:"Bebas Neue",sans-serif;font-weight:400;font-size:35px;margin-top:10px;line-height:36px}
.step p{font-size:13.5px;line-height:17px;margin-top:3px}

.stats{position:absolute;top:597px;left:0;width:1010px}
.stat{position:absolute;width:280px;text-align:center;transform:translateX(-50%)}
.stat h3{font-family:"Bebas Neue",sans-serif;font-weight:400;font-size:25px;margin-top:6px;line-height:26px}
.stat .pct{font-family:"PT Sans",sans-serif;font-weight:700;font-size:35px;line-height:40px}
.stat p{font-size:13.5px;line-height:16px;margin-top:5px;text-transform:uppercase}

.fixture{position:absolute;top:795px;width:280px;height:210px;background:var(--card-bg);font-family:"Arimo",sans-serif}
.fixture .teams{display:flex;justify-content:space-between;padding:14px 15px 0;font-size:14px;color:#555}
.fixture .crest{position:absolute;top:45px;width:64px;height:64px;border-radius:50%}
.fixture .crest.home{left:25px;background:#c8202f}
.fixture .crest.away{right:25px;background:#e4b82c}
.fixture .vs{position:absolute;top:56px;width:100%;text-align:center;font-size:40px;color:#444}
.fixture .kick{position:absolute;top:141px;width:100%;text-align:center;font-size:11px;color:#555}
.fixture .predict{position:absolute;left:31px;top:164px;width:218px;height:31px;background:var(--teal);color:var(--white);font-size:14.5px;line-height:31px;text-align:center}

.footer{position:absolute;left:0;top:1052px;width:1010px;height:148px;background:var(--footer-bg);text-align:center;color:var(--white)}
.footer-links{margin-top:27px;font-size:12.5px;display:flex;justify-content:center;gap:26px}
.social{display:flex;justify-content:center;gap:17px;margin-top:17px}
.social span{width:28px;height:28px;border-radius:50%}
.copyright{margin-top:17px;font-size:10.5px;color:var(--muted)}
</style>
</head>
<body>
<header class="topbar">
  <div class="brand"><span class="brand-dot"></span>PitchTally</div>
  <nav class="main-nav">
    <a class="is-active" style="left:249px">HOME</a>
    <a style="left:327px">MINILIGA</a>
    <a style="left:407px">TABLES</a>
    <a style="left:475px">KITTY</a>
    <a style="left:537px">FAQ</a>
    <a style="left:594px">ME</a>
  </nav>
  <div class="signin">Sign in ⌄</div>
  <div class="search"><svg width="10" height="10" viewBox="0 0 10 10"><circle cx="4" cy="4" r="3" fill="none" stroke="#8a8a8a" stroke-width="1.3"/><line x1="6.3" y1="6.3" x2="9.3" y2="9.3" stroke="#8a8a8a" stroke-width="1.3"/></svg>Search</div>
</header>

<section class="hero">
  <div class="hero-photo" role="img" aria-label="Two footballers leaping for a ball under stadium lights"></div>
  <h1 class="hero-title">ALTOGETHER BETTER PREDICTIONS</h1>
  <p class="hero-lead">Predict results, scores and scorers for your free chance to win a £20 ShopNest voucher every week. Overall season winner gets up to £1000 in ShopNest vouchers! No entry fee and no catches.</p>
  <div class="join">JOIN NOW</div>

  <div class="step" style="left:50px">
    <div class="step-icon" style="background:var(--teal)">
      <svg width="34" height="38" viewBox="0 0 34 38"><path d="M9 17V11a8 8 0 0 1 16 0v6" fill="none" stroke="#fff" stroke-width="4"/><rect x="3" y="16" width="28" height="20" rx="2" fill="#fff"/><circle cx="17" cy="24" r="3" fill="#333"/><rect x="16" y="25" width="2" height="6" fill="#333"/></svg>
    </div>
    <h2>LOGIN</h2>
    <p>You can use your existing StakeLine or Fantasy Football login details.</p>
  </div>
  <div class="step" style="left:355px">
    <div class="step-icon" style="background:var(--blue)">
      <svg width="40" height="38" viewBox="0 0 40 38"><path d="M10 2h20v12a10 10 0 0 1-20 0z" fill="#fff"/><path d="M10 6H3c0 8 4 11 8 11M30 6h7c0 8-4 11-8 11" fill="none" stroke="#fff" stroke-width="3"/><rect x="18" y="23" width="4" height="7" fill="#fff"/><rect x="11" y="30" width="18" height="6" fill="#fff"/></svg>
    </div>
    <h2>PREDICT</h2>
    <p>The scores from the 6 matches in the current round.</p>
  </div>
  <div class="step" style="left:658px">
    <div class="step-icon" style="background:var(--gold)">
      <svg width="38" height="38" viewBox="0 0 38 38"><rect x="4" y="12" width="30" height="8" fill="#fff"/><rect x="6" y="20" width="26" height="16" fill="#fff"/><rect x="16" y="12" width="6" height="24" fill="#e0453a"/><path d="M19 12c-4-8-12-6-8 0M19 12c4-8 12-6 8 0" fill="none" stroke="#e0453a" stroke-width="3"/></svg>
    </div>
    <h2>ENJOY</h2>
    <p>Sit back as the goals go in, will you scoop the jackpot?</p>
  </div>
</section>

<section class="stats">
  <div class="stat" style="left:200px">
    <svg width="40" height="47" viewBox="0 0 40 47"><path d="M3 0h11l6 12 6-12h11L24 20H16z" fill="var(--teal)"/><circle cx="20" cy="31" r="15" fill="var(--gold)"/><circle cx="20" cy="31" r="11" fill="#e9c86a"/><path d="M20 23l2.4 5 5.4.6-4 3.7 1.1 5.3L20 35l-4.9 2.6 1.1-5.3-4-3.7 5.4-.6z" fill="#c99a2e"/></svg>
    <h3>RESULT</h3><div class="pct" style="color:var(--teal)">100%</div><p>Eastbridge United win</p>
  </div>
  <div class="stat" style="left:503px">
    <svg width="40" height="47" viewBox="0 0 40 47"><path d="M3 0h11l6 12 6-12h11L24 20H16z" fill="var(--teal)"/><circle cx="20" cy="31" r="15" fill="var(--gold)"/><circle cx="20" cy="31" r="11" fill="#e9c86a"/><path d="M20 23l2.4 5 5.4.6-4 3.7 1.1 5.3L20 35l-4.9 2.6 1.1-5.3-4-3.7 5.4-.6z" fill="#c99a2e"/></svg>
    <h3>SCORE</h3><div class="pct" style="color:var(--blue)">100%</div><p>Marston Vale 0 Northport<br>United 2</p>
  </div>
  <div class="stat" style="left:808px">
    <svg width="40" height="47" viewBox="0 0 40 47"><path d="M3 0h11l6 12 6-12h11L24 20H16z" fill="var(--teal)"/><circle cx="20" cy="31" r="15" fill="var(--gold)"/><circle cx="20" cy="31" r="11" fill="#e9c86a"/><path d="M20 23l2.4 5 5.4.6-4 3.7 1.1 5.3L20 35l-4.9 2.6 1.1-5.3-4-3.7 5.4-.6z" fill="#c99a2e"/></svg>
    <h3>1ST GOAL</h3><div class="pct" style="color:var(--gold)">57%</div><p>Dylan R</p>
  </div>
</section>

<article class="fixture" style="left:61px">
  <div class="teams"><span>Merseyford FC</span><span>Castile Real</span></div>
  <span class="crest home"></span><span class="vs">VS</span><span class="crest away"></span>
  <div class="kick">14 October 2013, 23:00 (FT)</div>
  <div class="predict">PREDICT SCORE NOW</div>
</article>
<article class="fixture" style="left:365px">
  <div class="teams"><span>Merseyford FC</span><span>Castile Real</span></div>
  <span class="crest home"></span><span class="vs">VS</span><span class="crest away"></span>
  <div class="kick">14 October 2013, 23:00 (FT)</div>
  <div class="predict">PREDICT SCORE NOW</div>
</article>
<article class="fixture" style="left:668px">
  <div class="teams"><span>Merseyford FC</span><span>Castile Real</span></div>
  <span class="crest home"></span><span class="vs">VS</span><span class="crest away"></span>
  <div class="kick">14 October 2013, 23:00 (FT)</div>
  <div class="predict">PREDICT SCORE NOW</div>
</article>

<footer class="footer">
  <nav class="footer-links"><span>About</span><span>Terms</span><span>Site Map</span><span>Privacy</span><span>Contact Us</span></nav>
  <div class="social">
    <span style="background:#3b5a9a"></span>
    <span style="background:#2aa9e0"></span>
    <span style="background:#ea4c89"></span>
    <span style="background:#1ab7ea"></span>
    <span style="background:#e0453a"></span>
  </div>
  <p class="copyright">© PitchTally 2014 – All Right Reserved</p>
</footer>
</body>
</html>
```